Law Firm Header Revision

Task: Redesign my law firm Word document header (modern, succinct, logo-first, easy address updates)

I need you to revise and modernize my Microsoft Word document header for Law Office of Bram Holcott, PLLC. The result should look professional and clean on letters (including Letters of Protection), with the logo as the main focus and the text kept succinct.

Goals:
1. Create a modern, minimal header that feels premium and uncluttered.
Make the logo the most visually dominant element.
Reduce the visual weight of the contact/address block so it doesn’t distract from the document.
Make the address easy to change later (I’m moving offices soon) while keeping the same header design.

2. Content to include (keep all info accurate):
Law Office of Bram Holcott, PLLC
615 Pemberly St. Ste #300-214, Houston, TX 77002
Office: 832.555.0143
Direct: 713.555.0187
Fax: 832.555.0129
Bholcottlaw.com

3. Layout requirements:
Provide 3 header style options:
Logo left + contact info right
Centered logo + single concise contact line below
Logo left + firm name prominent + minimal contact line
The primary line near the logo should be minimal (preferably website + main office phone).
The address should be easy to update in one place without redesigning the header. Prefer either:
Move the full address to the footer, or
Put the address in a single dedicated line/block so I can edit it once and keep the layout unchanged.
4. Build constraints:
Must be achievable using standard Microsoft Word tools only (header/footer, tables, alignment, fonts, spacing). No advanced graphics software.
Provide exact header text, plus step-by-step Word instructions for each option:
Font recommendations + sizes
Alignment
Spacing
Table setup (if used)
How to keep it consistent across pages

5. Deliverable:
For each of the 3 options, provide:
The exact header content (with line breaks)
Formatting specs (fonts, sizes, spacing)
Word build steps so I can recreate it reliably and keep the logo as the focal point.

```html
<!DOCTYPE html>
<html lang="en">
<head>
<meta charset="utf-8">
<title>Law Office of Bram Holcott, PLLC – Letterhead Options</title>
<link rel="stylesheet" href="https://fonts.googleapis.com/css2?family=Roboto:wght@400;500&display=swap">
<style>
  :root {
    --backdrop: #a1a1a1;
    --paper: #ffffff;
    --navy: #13223f;
    --gold: #b8955a;
    --ink: #1e2330;
    --watermark: #eeeef1;
  }
  * { margin: 0; padding: 0; box-sizing: border-box; }
  html, body { width: 1200px; height: 564px; overflow: hidden; background: var(--backdrop); }
  body { position: relative; font-family: "Roboto", Arial, sans-serif; color: var(--ink); }

  .sheet { position: absolute; top: 14px; width: 378px; height: 535px; background: var(--paper); overflow: hidden; }
  .sheet--one { left: 16px; }
  .sheet--two { left: 410px; }
  .sheet--three { left: 796px; }

  .sheet__decor { position: absolute; inset: 0; width: 378px; height: 535px; }
  .band { fill: var(--navy); }
  .band-edge { fill: none; stroke: var(--gold); stroke-width: 0.8; }

  /* brand */
  .brand { position: absolute; display: flex; align-items: center; gap: 5px; }
  .brand__square { width: 24px; height: 24px; background: var(--navy); flex: none; }
  .brand__name { font-weight: 400; color: var(--navy); font-size: 15px; letter-spacing: 0.2px; white-space: nowrap; }
  .brand--small .brand__square { width: 19px; height: 19px; }
  .brand--small .brand__name { font-size: 12.5px; }

  .firm-name { position: absolute; font-size: 6px; color: var(--ink); white-space: nowrap; }

  /* contact lines */
  .contact { position: absolute; font-size: 5.8px; color: var(--ink); }
  .contact__item { display: flex; align-items: center; gap: 4px; white-space: nowrap; height: 11.5px; }
  .contact--row { display: flex; gap: 8px; }
  .icon { width: 6px; height: 6px; fill: var(--gold); flex: none; }

  /* divider rule */
  .rule { position: absolute; left: 43px; width: 291px; height: 3px; }
  .rule__thin { position: absolute; left: 0; right: 0; top: 1px; height: 0.7px; background: var(--navy); }
  .rule__bold { position: absolute; left: 64px; width: 150px; top: 0; height: 2.6px; background: var(--gold); }

  /* faint mark */
  .backmark { position: absolute; left: 66px; top: 241px; display: flex; align-items: center; gap: 8px; }
  .backmark__square { width: 56px; height: 56px; background: var(--watermark); }
  .backmark__name { font-size: 30px; color: var(--watermark); white-space: nowrap; letter-spacing: 0.5px; }

  /* footer */
  .footer-info { position: absolute; top: 502px; left: 0; width: 378px; font-size: 5.2px; color: var(--ink); line-height: 7.6px; }
  .footer-info__item { position: absolute; display: flex; gap: 3px; }
  .footer-info__item .icon { width: 7px; height: 7px; margin-top: 1px; }
  .footer-info__address { left: 67px; }
  .footer-info__phone { left: 193px; }
  .footer-info__fax { left: 263px; top: -1px; }
  .footer-rule { position: absolute; left: 70px; width: 238px; top: 522px; height: 0.5px; background: #9a9fab; }
  .doc-label { position: absolute; top: 526px; left: 70px; width: 238px; text-align: center; font-size: 4.2px; color: var(--ink); letter-spacing: 0.1px; }
  .page-number { position: absolute; top: 520px; left: 345px; font-size: 5px; font-weight: 500; color: #ffffff; letter-spacing: 0.2px; }
</style>
</head>
<body>

<svg width="0" height="0" style="position:absolute">
  <defs>
    <symbol id="i-phone" viewBox="0 0 24 24"><path d="M6.6 10.8a15.1 15.1 0 0 0 6.6 6.6l2.2-2.2c.3-.3.7-.4 1-.2 1.1.4 2.3.6 3.6.6.6 0 1 .4 1 1V20c0 .6-.4 1-1 1A17 17 0 0 1 3 4c0-.6.4-1 1-1h3.5c.6 0 1 .4 1 1 0 1.3.2 2.5.6 3.6.1.3 0 .7-.2 1z"/></symbol>
    <symbol id="i-globe" viewBox="0 0 24 24"><path d="M12 2a10 10 0 1 0 0 20 10 10 0 0 0 0-20zm6.9 6h-2.9a15.6 15.6 0 0 0-1.4-3.6A8 8 0 0 1 18.9 8zM12 4c.8 1.2 1.5 2.5 1.9 4h-3.8c.4-1.5 1.1-2.8 1.9-4zM4.3 14a8.2 8.2 0 0 1 0-4h3.4a16.5 16.5 0 0 0 0 4zm.8 2H8c.3 1.3.8 2.5 1.4 3.6A8 8 0 0 1 5.1 16zM8 8H5.1a8 8 0 0 1 4.3-3.6C8.8 5.5 8.4 6.7 8 8zm4 12c-.8-1.2-1.5-2.5-1.9-4h3.8c-.4 1.5-1.1 2.8-1.9 4zm2.3-6H9.7a14.7 14.7 0 0 1 0-4h4.6a14.7 14.7 0 0 1 0 4zm.3 5.6c.6-1.1 1.1-2.3 1.4-3.6h2.9a8 8 0 0 1-4.3 3.6zm1.7-5.6a16.5 16.5 0 0 0 0-4h3.4a8.2 8.2 0 0 1 0 4z"/></symbol>
    <symbol id="i-pin" viewBox="0 0 24 24"><path d="M12 2a7 7 0 0 0-7 7c0 5.2 7 13 7 13s7-7.8 7-13a7 7 0 0 0-7-7zm0 9.5a2.5 2.5 0 1 1 0-5 2.5 2.5 0 0 1 0 5z"/></symbol>
    <symbol id="i-fax" viewBox="0 0 24 24"><path d="M19 8H5a3 3 0 0 0-3 3v6h4v4h12v-4h4v-6a3 3 0 0 0-3-3zm-3 11H8v-5h8zm3-7a1 1 0 1 1 0-2 1 1 0 0 1 0 2zM18 3H6v4h12z"/></symbol>
    <symbol id="sheet-frame" viewBox="0 0 378 535">
      <path class="band" d="M21,0 C26,0 28,19 40,19 L146,19 C157,19 160,0 167,0 Z"/>
      <path class="band-edge" d="M14,0 C22,2 24,22 40,22 L146,22 C162,22 162,4 172,0"/>
      <path class="band" d="M212,0 C218,0 222,19 234,19 L352,19 C360,19 362,0 368,0 Z"/>
      <path class="band-edge" d="M206,0 C214,2 216,22 234,22 L352,22 C364,22 364,4 378,1"/>
      <path class="band" d="M0,496 C30,496 38,500 48,515 C56,528 62,535 77,535 L0,535 Z"/>
      <path class="band-edge" d="M0,489 C34,489 42,494 52,510 C60,524 68,535 86,535"/>
      <path class="band" d="M301,535 C318,535 322,525 332,511 C342,497 350,496 378,496 L378,535 Z"/>
      <path class="band-edge" d="M292,535 C310,535 316,522 326,507 C336,492 346,489 378,488"/>
    </symbol>
  </defs>
</svg>

<!-- Option 1: logo left, contact right -->
<section class="sheet sheet--one">
  <svg class="sheet__decor"><use href="#sheet-frame"/></svg>
  <div class="brand" style="left:44px; top:44px;">
    <span class="brand__square"></span><span class="brand__name">BRAM HOLCOTT</span>
  </div>
  <div class="contact" style="left:260px; top:45px;">
    <div class="contact__item"><svg class="icon"><use href="#i-phone"/></svg>Office - 832.555.0143</div>
    <div class="contact__item"><svg class="icon"><use href="#i-globe"/></svg>Website - Bholcottlaw.com</div>
  </div>
  <div class="rule" style="top:85px;"><span class="rule__thin"></span><span class="rule__bold"></span></div>
  <div class="backmark"><span class="backmark__square"></span><span class="backmark__name">BRAM HOLCOTT</span></div>
  <div class="footer-info">
    <div class="footer-info__item footer-info__address"><svg class="icon"><use href="#i-pin"/></svg><span>Address : 615 Pemberly St. Ste #300-214,<br>Houston, TX 77002</span></div>
    <div class="footer-info__item footer-info__phone"><svg class="icon"><use href="#i-phone"/></svg><span>Phone Number :<br>713.555.0187</span></div>
    <div class="footer-info__item footer-info__fax"><svg class="icon"><use href="#i-fax"/></svg><span>Fax Number :<br>832.555.0129</span></div>
  </div>
  <div class="footer-rule"></div>
  <div class="doc-label">LETTTER OF PROTECTION</div>
  <div class="page-number">PAGE 1</div>
</section>

<!-- Option 2: centred logo, single contact line -->
<section class="sheet sheet--two">
  <svg class="sheet__decor"><use href="#sheet-frame"/></svg>
  <div class="brand" style="left:137px; top:37px;">
    <span class="brand__square"></span><span class="brand__name">BRAM HOLCOTT</span>
  </div>
  <div class="contact contact--row" style="left:115px; top:67px;">
    <div class="contact__item"><svg class="icon"><use href="#i-phone"/></svg>Office - 832.555.0143</div>
    <div class="contact__item"><svg class="icon"><use href="#i-globe"/></svg>Website - Bholcottlaw.com</div>
  </div>
  <div class="rule" style="top:90px;"><span class="rule__thin"></span><span class="rule__bold"></span></div>
  <div class="backmark"><span class="backmark__square"></span><span class="backmark__name">BRAM HOLCOTT</span></div>
  <div class="footer-info">
    <div class="footer-info__item footer-info__address"><svg class="icon"><use href="#i-pin"/></svg><span>Address : 615 Pemberly St. Ste #300-214,<br>Houston, TX 77002</span></div>
    <div class="footer-info__item footer-info__phone"><svg class="icon"><use href="#i-phone"/></svg><span>Phone Number :<br>713.555.0187</span></div>
    <div class="footer-info__item footer-info__fax"><svg class="icon"><use href="#i-fax"/></svg><span>Fax Number :<br>832.555.0129</span></div>
  </div>
  <div class="footer-rule"></div>
  <div class="doc-label">LETTTER OF PROTECTION</div>
</section>

<!-- Option 3: logo left with firm name, contact right -->
<section class="sheet sheet--three">
  <svg class="sheet__decor"><use href="#sheet-frame"/></svg>
  <div class="brand brand--small" style="left:44px; top:36px;">
    <span class="brand__square"></span><span class="brand__name">BRAM HOLCOTT</span>
  </div>
  <div class="firm-name" style="left:44px; top:60px;">Law Office of Bram Holcott, PLLC</div>
  <div class="contact" style="left:258px; top:43px;">
    <div class="contact__item"><svg class="icon"><use href="#i-phone"/></svg>Office - 832.555.0143</div>
    <div class="contact__item"><svg class="icon"><use href="#i-globe"/></svg>Website - Bholcottlaw.com</div>
  </div>
  <div class="rule" style="top:82px;"><span class="rule__thin"></span><span class="rule__bold"></span></div>
  <div class="backmark"><span class="backmark__square"></span><span class="backmark__name">BRAM HOLCOTT</span></div>
  <div class="footer-info">
    <div class="footer-info__item footer-info__address"><svg class="icon"><use href="#i-pin"/></svg><span>Address : 615 Pemberly St. Ste #300-214,<br>Houston, TX 77002</span></div>
    <div class="footer-info__item footer-info__phone"><svg class="icon"><use href="#i-phone"/></svg><span>Phone Number :<br>713.555.0187</span></div>
    <div class="footer-info__item footer-info__fax"><svg class="icon"><use href="#i-fax"/></svg><span>Fax Number :<br>832.555.0129</span></div>
  </div>
  <div class="footer-rule"></div>
  <div class="doc-label">LETTTER OF PROTECTION</div>
  <div class="page-number">PAGE 1</div>
</section>

</body>
</html>
```